Front and content page design for Fitness Cookbook

I am looking for someone to Design a front cover for a Recipe book and also create an amazing layout for the book.

Its for a corporate seminar so has to be eye catching, professional and bold.

Content is complete

Target Market(s)

Industry/Entity Type

Health And Wellness

Font styles to use
Sans Serif

Requirements
Must have
• Eye catching, professional and bold.
• By Dorian as stated on the document
• Must have Tidewell Motion Logo on it.

```html
<!DOCTYPE html>
<html lang="en">
<head>
<meta charset="utf-8">
<title>Protein and Fat Meals</title>
<link rel="stylesheet" href="https://fonts.googleapis.com/css2?family=Cabin:wght@400;500;600&display=swap">
<style>
  :root {
    --page: #ffffff;
    --brand-blue: #1f86c8;
    --ink: #2b2b2b;
    --tab-orange: #f39a1e;
    --logo-navy: #1d3f6e;
  }
  html, body {
    margin: 0;
    padding: 0;
    overflow: hidden;
    background: var(--page);
  }
  .page {
    position: relative;
    width: 849px;
    height: 1200px;
    background: var(--page);
    font-family: "Cabin", "Gill Sans", sans-serif;
    color: var(--ink);
    overflow: hidden;
  }
  .chapter-title {
    position: absolute;
    left: 55px;
    top: 78px;
    margin: 0;
    font-size: 60px;
    font-weight: 500;
    letter-spacing: -0.5px;
    color: var(--brand-blue);
    line-height: 1;
  }
  .section-tab {
    position: absolute;
    right: 0;
    top: 119px;
    width: 31px;
    height: 320px;
    background: var(--tab-orange);
  }
  .info-block {
    position: absolute;
    left: 57px;
    width: 720px;
  }
  .info-block.best-used { top: 182px; }
  .info-block.why-eat { top: 356px; }
  .info-heading {
    margin: 0 0 8px;
    font-size: 26px;
    font-weight: 500;
    color: var(--brand-blue);
    letter-spacing: 0.3px;
    line-height: 1.1;
  }
  .info-list {
    list-style: none;
    margin: 0;
    padding: 0;
    font-size: 16px;
    font-weight: 600;
    line-height: 22.6px;
  }
  .info-list li::before {
    content: "\2022";
    margin-right: 5px;
  }
  .page-footer {
    position: absolute;
    right: 12px;
    bottom: 30px;
    display: flex;
    align-items: center;
    gap: 14px;
  }
  .brand-mark {
    display: flex;
    align-items: center;
    gap: 4px;
    font-size: 11px;
    font-weight: 600;
    color: var(--logo-navy);
  }
  .brand-mark .brand-square {
    width: 10px;
    height: 10px;
    background: var(--logo-navy);
  }
  .page-number {
    font-size: 15px;
    font-weight: 500;
    color: var(--ink);
  }
</style>
</head>
<body>
  <main class="page">
    <h1 class="chapter-title">Protein and Fat Meals</h1>
    <div class="section-tab"></div>

    <section class="info-block best-used">
      <h2 class="info-heading">BEST USED</h2>
      <ul class="info-list">
        <li>Anytime of the day other than around training (goal dependent)</li>
        <li>Rest days</li>
        <li>Breakfasts (especially meals containing red meat)</li>
        <li>During a low carb or ‘reset’ plan/phase</li>
      </ul>
    </section>

    <section class="info-block why-eat">
      <h2 class="info-heading">WHY EAT THESE MEALS</h2>
      <ul class="info-list">
        <li>To help regulate blood sugar levels throughout the day</li>
        <li>To ‘teach’ your body to use fats as fuel, resulting in greater fat loss long term</li>
        <li>To keep you fuller for longer</li>
        <li>To help ‘clean out’ your digestive system and liver pathways</li>
        <li>Increase mental focus and awareness</li>
      </ul>
    </section>

    <footer class="page-footer">
      <div class="brand-mark">
        <span class="brand-square"></span>
        <span class="brand-name">Tidewell Motion</span>
      </div>
      <span class="page-number">5</span>
    </footer>
  </main>
</body>
</html>
```